Kestrel Hearth Business Card Design

Design new, 2 sides, business cards for a residential and light commercial heating, air conditioning contractor.

Target Market(s)

Homeowners, small businesses

Industry/Entity Type

Business

Contact Information for Business Card

Dominic Westerhall
Phone - 862-415-2736
Email
Address - PO box 518
Brightwater NJ 07912
Website - www.HarborBreezeLLC.example

Requirements
Must have
• logo, company colors, standard size with no die cut, so I can use nova stamp

```html
<!DOCTYPE html>
<html lang="en">
<head>
<meta charset="utf-8">
<title>Kestrel Hearth Business Card</title>
<link href="https://fonts.googleapis.com/css2?family=Source+Sans+3:ital,wght@0,400;0,600;1,400&display=swap" rel="stylesheet">
<style>
  :root {
    --maroon: #9b1d35;
    --orange: #f08a1e;
    --cream: #fbe3b0;
    --ink: #4a4a4a;
    --paper: #ffffff;
    --backdrop: #e9e6e1;
  }
  * { box-sizing: border-box; margin: 0; padding: 0; }
  html, body {
    width: 1200px; height: 950px; overflow: hidden;
    background: var(--backdrop);
    font-family: "Source Sans 3", sans-serif;
  }
  .canvas {
    width: 1200px; height: 950px;
    display: flex; flex-direction: column; align-items: center; justify-content: center; gap: 40px;
  }
  .card {
    width: 720px; height: 411px; position: relative; overflow: hidden;
    box-shadow: 0 6px 18px rgba(0,0,0,.18);
  }
  .card-front { background: var(--paper); }
  .card-front .edge {
    position: absolute; left: 0; right: 0; bottom: 0; height: 10px;
    background: var(--maroon); border-top: 3px solid var(--orange);
  }
  .brand {
    position: absolute; display: flex; align-items: center; gap: 12px;
    font-weight: 600; color: var(--maroon); white-space: nowrap;
  }
  .brand .dot { width: 20px; height: 20px; border-radius: 50%; background: var(--orange); flex: none; }
  .card-front .brand { left: 54px; top: 154px; font-size: 30px; }
  .divider {
    position: absolute; left: 330px; top: 40px; bottom: 50px; width: 1px;
    background: var(--orange);
  }
  .contact {
    position: absolute; right: 50px; top: 44px; text-align: right; color: var(--ink);
  }
  .contact .name { font-size: 24px; font-weight: 600; color: var(--maroon); letter-spacing: .5px; }
  .contact .role { font-size: 17px; color: var(--orange); margin-bottom: 18px; }
  .contact .line { font-size: 17px; display: flex; justify-content: flex-end; align-items: center; gap: 10px; line-height: 30px; }
  .contact .line svg { width: 16px; height: 16px; fill: var(--maroon); }
  .contact .email { font-size: 17px; margin-top: 22px; }
  .address {
    position: absolute; left: 54px; bottom: 48px; color: var(--ink); font-size: 17px; line-height: 25px;
  }
  .address .web { color: var(--maroon); }
  .card-back { background: var(--maroon); }
  .card-back .brand { left: 380px; top: 155px; font-size: 36px; color: var(--cream); }
  .tagline {
    position: absolute; left: 60px; bottom: 60px; color: var(--cream);
    font-style: italic; font-size: 19px; line-height: 26px;
  }
</style>
</head>
<body>
<main class="canvas">
  <section class="card card-front" aria-label="Business card front">
    <div class="brand"><span class="dot"></span>Kestrel Hearth</div>
    <div class="divider"></div>
    <div class="contact">
      <div class="name">DOMINIC WESTERHALL</div>
      <div class="role">CEO/Founder</div>
      <div class="line">862 415 2736
        <svg viewBox="0 0 16 16" aria-hidden="true"><path d="M3 1h3l1 4-2 1c1 2 3 4 5 5l1-2 4 1v3c0 1-1 2-2 2C7 15 1 9 1 3c0-1 1-2 2-2z"/></svg></div>
      <div class="line">862 415 2790
        <svg viewBox="0 0 16 16" aria-hidden="true"><path d="M4 0h8v16H4zM5.5 2v11h5V2z"/></svg></div>
      <div class="line">862 415 2755
        <svg viewBox="0 0 16 16" aria-hidden="true"><path d="M1 5h14v8H1zM4 1h8v3H4zM4 10h8v5H4z"/></svg></div>
      <div class="email">dominic@kestrelhearthllc.example</div>
    </div>
    <div class="address">
      PO box 518<br>
      Brightwater NJ 07912<br>
      <span class="web">www.KestrelHearthLLC.example</span>
    </div>
    <div class="edge"></div>
  </section>

  <section class="card card-back" aria-label="Business card back">
    <div class="brand"><span class="dot"></span>Kestrel Hearth</div>
    <p class="tagline">Residential &amp; light commercial heating<br>Air conditioning contractor</p>
  </section>
</main>
</body>
</html>
```